Automotive eCommerce Business looking for a business card design

Looking for a clean and simple business card design. Our company name is "Brindle Auto" and we are a company specializing in the ecommerce sales of automotive parts, specifically for pick up trucks and large SUVs. Our company colours are red, black, and white.

Feel free to use the logo provided or create a new logo that you seem fit. Looking forward to your creative ideas!

Industry/Entity Type

Automotive

Contact Information for Business Card

We were thinking of a possibly two-sided design featuring just the logo and company name on one side, and personal information on the other side. Single sided designs will be considered as well.

Font styles to use
Serif
Sans Serif
Decorative

Colors
ec1f27
ffffff
000000

Requirements
Must have
• Space for employee's name, title, phone number and email address, along with the company address and website somewhere.

```html
<!DOCTYPE html>
<html lang="en">
<head>
<meta charset="utf-8">
<title>Brindle Auto Ltd. — Business Card</title>
<link rel="stylesheet" href="https://fonts.googleapis.com/css2?family=Ubuntu:wght@400;500;700&display=swap">
<style>
  :root {
    --brand-red: #ec1f27;
    --brand-white: #ffffff;
    --brand-black: #000000;
    --card-top: #1f1e1f;
    --card-bottom: #0b0b0b;
    --text-muted: #bdbdbd;
    --page-bg: #e6e3df;
  }
  * { margin: 0; padding: 0; box-sizing: border-box; }
  html, body { width: 1200px; height: 675px; overflow: hidden; }
  body {
    background: var(--page-bg);
    font-family: "Ubuntu", sans-serif;
    display: flex;
    align-items: center;
    justify-content: center;
    gap: 60px;
  }
  .card {
    position: relative;
    width: 510px;
    height: 292px;
    background: linear-gradient(160deg, var(--card-top), var(--card-bottom));
    color: var(--brand-white);
    box-shadow: 0 10px 26px rgba(0,0,0,0.25);
  }
  .brand {
    display: flex;
    flex-direction: column;
    align-items: center;
    gap: 16px;
  }
  .brand-mark {
    width: 74px;
    height: 74px;
    background: var(--brand-red);
  }
  .brand-name {
    font-weight: 700;
    font-size: 24px;
    letter-spacing: 0.5px;
    color: var(--brand-white);
  }
  .card--front {
    display: flex;
    align-items: center;
    justify-content: center;
  }
  .card--back .brand {
    position: absolute;
    top: 34px;
    left: 250px;
    gap: 10px;
  }
  .card--back .brand-mark { width: 58px; height: 58px; }
  .card--back .brand-name { font-size: 17px; }
  .person {
    position: absolute;
    top: 60px;
    left: 34px;
    line-height: 1.4;
  }
  .person-name {
    color: var(--brand-red);
    font-weight: 500;
    font-size: 16px;
    letter-spacing: 0.6px;
    text-transform: uppercase;
  }
  .person-title, .person-address {
    color: var(--text-muted);
    font-size: 12.5px;
  }
  .contacts {
    position: absolute;
    left: 276px;
    bottom: 34px;
    list-style: none;
    font-size: 12.5px;
    color: var(--text-muted);
    line-height: 1.55;
    letter-spacing: 0.4px;
  }
  .contacts li { display: flex; align-items: center; gap: 9px; }
  .contacts svg { width: 10px; height: 10px; fill: var(--brand-red); flex: none; }
</style>
</head>
<body>
  <section class="card card--front" aria-label="Card front">
    <div class="brand">
      <div class="brand-mark"></div>
      <div class="brand-name">BRINDLE AUTO LTD.</div>
    </div>
  </section>

  <section class="card card--back" aria-label="Card back">
    <div class="brand">
      <div class="brand-mark"></div>
      <div class="brand-name">BRINDLE AUTO LTD.</div>
    </div>

    <div class="person">
      <p class="person-name">Marcus Delaney</p>
      <p class="person-title">Managing Director</p>
      <p class="person-address">1480 Harbor Ave<br>Fairview, LA 70912</p>
    </div>

    <ul class="contacts">
      <li>
        <svg viewBox="0 0 10 10" aria-hidden="true"><path d="M2 0.5 L3.6 0.5 L4.2 2.8 L3 3.6 Q4 5.8 6.4 7 L7.2 5.8 L9.5 6.4 L9.5 8 Q9.5 9.5 8 9.5 Q0.5 8.5 0.5 2 Q0.5 0.5 2 0.5Z"/></svg>
        555 014 2387
      </li>
      <li>
        <svg viewBox="0 0 10 10" aria-hidden="true"><path d="M0.5 2 H9.5 V8.5 H0.5Z M0.5 2 L5 5.5 L9.5 2" stroke="#1a1a1a" stroke-width="0.8"/></svg>
        marcus@brindleautoltd.com
      </li>
      <li>
        <svg viewBox="0 0 10 10" aria-hidden="true"><circle cx="5" cy="5" r="4.5"/><path d="M0.5 5 H9.5 M5 0.5 Q2.5 5 5 9.5 M5 0.5 Q7.5 5 5 9.5" stroke="#1a1a1a" stroke-width="0.7" fill="none"/></svg>
        www.brindleautoltd.com
      </li>
    </ul>
  </section>
</body>
</html>
```